Plume Arc Website - Enabling Omni channel

Slogan : Enabling Omnichannel Sales

1. Sell products via multiple sale channels
2. Access our technology and services to get your products moving through new channels
3. Customise our mobile and web technology platforms to suit your supply chain.

Slogan: Plume arc – Innovating new business.

Use the content from these websites to create a new one
http://vorbankhq.com/
http://lorvane-designs.com/plumeArc02/

Target Market(s)

Business and Coporations who need mobile and web technology or services to increase product sales within their vertical industry. Our case studies show the industries we have worked in; namely: Retail, wholesale, online retail, motor and auto trade. Also have rich experience in Importing and Exporting.

Industry/Entity Type

Retail

Number of Pages Required

3 page

Font styles to use
Sans Serif

Colors
0255a3
ec1f27
9bcb3c
ffffff
0792cd
ffc214

Requirements
Must have
• Punchy headline home page with possible animations or unique and interesting images

```html
<!DOCTYPE html>
<html lang="en">
<head>
<meta charset="utf-8">
<title>Plume Arc – Innovating New Business</title>
<link href="https://fonts.googleapis.com/css2?family=Open+Sans:wght@400;600;700&display=swap" rel="stylesheet">
<style>
:root{
  --blue:#1a86c8;
  --blue-deep:#0f6fae;
  --green:#6da528;
  --green-dark:#558a1a;
  --ink:#2e2e2e;
  --text:#555;
  --grey-bg:#ececec;
  --rule:#d6d6d6;
  --dark:#1f2326;
  --white:#fff;
  --lime:#9bcb3c;
}
*{box-sizing:border-box;margin:0;padding:0}
html,body{width:1200px;height:3644px;overflow:hidden}
body{font-family:"Open Sans",Arial,sans-serif;color:var(--text);background:var(--white);position:relative}
.abs{position:absolute}
/* header */
.site-header{position:absolute;left:0;top:0;width:1200px;height:114px;background:var(--white);border-bottom:1px solid #e4e4e4}
.brand{position:absolute;left:112px;top:30px}
.brand-name{display:flex;align-items:center;gap:8px;font-size:27px;font-weight:700;color:var(--blue-deep);line-height:1}
.brand-dot{width:13px;height:13px;border-radius:50%;background:var(--blue)}
.brand-tag{font-size:10.5px;font-weight:600;color:var(--ink);margin-top:10px;letter-spacing:.3px}
.main-nav a{position:absolute;top:0;height:114px;padding-top:50px;transform:translateX(-50%);font-size:12px;font-weight:700;color:var(--ink);text-decoration:none;white-space:nowrap;text-align:center}
.main-nav a.active{color:var(--green);border-bottom:4px solid var(--green);width:97px}
/* hero */
.hero{position:absolute;left:0;top:114px;width:1200px;height:498px;background:linear-gradient(90deg,#f3f5f6 0%,#e9ecee 45%,#cfd5da 100%);overflow:hidden}
.hero-photo{position:absolute;right:0;top:0;width:650px;height:498px;background:linear-gradient(100deg,rgba(233,236,238,0) 0%,#b9c0c6 30%,#3a3f45 62%,#8f98a0 100%)}
.hero-title{position:absolute;left:146px;top:212px;width:720px;font-size:28px;font-weight:600;color:var(--ink);line-height:1.38;letter-spacing:.3px}
.hero-text{position:absolute;left:146px;top:306px;width:520px;font-size:12.5px;color:#444;line-height:1.9}
.slide-arrow{position:absolute;top:231px;width:34px;height:34px;border-radius:50%;border:1px solid rgba(120,120,120,.45);background:rgba(255,255,255,.4)}
/* welcome */
.welcome{position:absolute;left:0;top:612px;width:1200px;height:452px;background:linear-gradient(120deg,#2a8fcf 0%,#1f7fc0 55%,#2c8ccb 100%);text-align:center;color:var(--white)}
.section-title{font-size:32px;font-weight:400;letter-spacing:.5px}
.divider-icon{display:flex;align-items:center;justify-content:center;gap:14px;margin:18px auto 0}
.divider-icon span{display:block;width:130px;height:1px;background:currentColor;opacity:.55}
.welcome .section-title{padding-top:98px}
.welcome p{width:700px;margin:36px auto 0;font-size:12.5px;line-height:2.3}
.btn-outline{display:inline-flex;align-items:center;gap:8px;margin-top:30px;padding:14px 44px;border:2px solid rgba(255,255,255,.85);color:var(--white);font-size:13px;font-weight:600;text-decoration:none}
/* solutions */
.solutions{position:absolute;left:0;top:1064px;width:1200px;height:442px;background:var(--grey-bg);text-align:center}
.solutions .section-title{padding-top:82px;color:var(--ink)}
.solutions .divider-icon{color:#777}
.solution-card{position:absolute;top:180px;width:222px;height:142px;background:var(--white);padding:5px;box-shadow:0 2px 5px rgba(0,0,0,.25)}
.solution-card .photo{position:relative;width:212px;height:132px}
.solution-card .label{position:absolute;left:0;bottom:0;width:100%;height:40px;line-height:40px;background:rgba(0,0,0,.62);color:var(--white);font-size:12px}
.dots{position:absolute;top:366px;left:585px;display:flex;gap:10px}
.dots i{width:11px;height:11px;border-radius:50%;background:#b7c2c9}
.dots i.on{background:var(--blue)}
/* features */
.features{position:absolute;left:0;top:1506px;width:1200px;height:491px;background:var(--white)}
.col-title{position:absolute;top:64px;font-size:24px;font-weight:600;color:var(--ink)}
.col-rule{position:absolute;top:110px;height:1px;background:var(--rule)}
.col-icon{position:absolute;top:100px}
.bullets{position:absolute;list-style:none}
.bullets li{font-size:12.5px;color:#555;line-height:19px;margin-bottom:19px;padding-left:16px;position:relative}
.bullets li::before{content:"";position:absolute;left:0;top:6px;border-left:6px solid var(--lime);border-top:4px solid transparent;border-bottom:4px solid transparent}
.btn-green{display:inline-flex;align-items:center;justify-content:center;gap:10px;background:linear-gradient(#7cb631,var(--green-dark));color:var(--white);font-size:13px;font-weight:600;text-decoration:none;border-radius:2px}
/* services */
.services{position:absolute;left:0;top:1997px;width:1200px;height:610px;background:linear-gradient(120deg,#4a4f54 0%,#2f3338 45%,#23272a 100%);text-align:center;color:var(--white)}
.services .section-title{padding-top:78px}
.services .lead{margin-top:20px;font-size:12.5px}
.service-card{position:absolute;top:243px;width:223px;height:251px;background:#e9ebec;color:var(--ink)}
.service-card .icon-box{position:absolute;left:42px;top:0;width:139px;height:107px;background:var(--blue);display:flex;align-items:center;justify-content:center}
.service-card h3{position:absolute;top:136px;left:0;width:100%;font-size:14px;font-weight:700;line-height:1.4}
.service-card p{position:absolute;left:24px;width:175px;font-size:12px;color:#555;line-height:2}
/* what to do */
.what-now{position:absolute;left:0;top:2607px;width:1200px;height:370px;background:var(--white)}
.what-photo{position:absolute;left:112px;top:66px;width:330px;height:232px;background:var(--white);padding:5px;box-shadow:0 2px 6px rgba(0,0,0,.28)}
.what-photo div{width:100%;height:100%;background:linear-gradient(135deg,#dfe8ef 0%,#8fb6d8 45%,#2f6fa9 100%)}
.what-now h2{position:absolute;left:476px;top:62px;font-size:24px;font-weight:600;color:var(--ink)}
.what-now p{position:absolute;left:476px;top:140px;width:612px;font-size:12.5px;line-height:2.2;color:#555}
/* partner */
.partner{position:absolute;left:0;top:2977px;width:1200px;height:386px;background:linear-gradient(180deg,#1b84c6 0%,#2b8fcf 60%,#3a98d4 100%);text-align:center;color:var(--white)}
.partner .section-title{padding-top:108px;font-weight:600}
.partner p{width:920px;margin:30px auto 0;font-size:12px;line-height:2.7}
/* footer */
.site-footer{position:absolute;left:0;top:3363px;width:1200px;height:202px;background:var(--dark)}
.footer-col{position:absolute;top:34px;color:#d8d8d8}
.footer-col h4{font-size:15px;font-weight:600;color:var(--white);letter-spacing:.5px;margin-bottom:14px}
.footer-col p{font-size:12px;line-height:1.6}
.social{display:flex;gap:10px;margin-top:24px}
.social i{width:30px;height:30px;border-radius:50%;border:1px solid #8c8c8c;display:block}
.newsletter-form{display:flex;margin-top:26px;width:288px;height:36px}
.newsletter-form span{flex:1;background:var(--white);font-size:12px;color:#777;padding:10px 12px}
.newsletter-form b{width:40px;background:var(--green);display:flex;align-items:center;justify-content:center;border:3px solid var(--white)}
.contact-line{display:flex;align-items:center;gap:14px;font-size:12px;margin-top:18px}
.contact-line i{width:30px;height:30px;border-radius:50%;border:1px solid #8c8c8c;display:flex;align-items:center;justify-content:center}
.bottom-bar{position:absolute;left:0;top:3565px;width:1200px;height:79px;background:var(--blue);color:#dbeefa;font-size:11.5px;text-align:center;line-height:79px}
</style>
</head>
<body>

<header class="site-header">
  <div class="brand">
    <div class="brand-name"><span class="brand-dot"></span>Plume Arc</div>
    <div class="brand-tag">INNOVATING NEW BUSINESS</div>
  </div>
  <nav class="main-nav">
    <a href="#" class="active" style="left:505px">HOME</a>
    <a href="#" style="left:608px">ABOUT US</a>
    <a href="#" style="left:719px">WHY US..?</a>
    <a href="#" style="left:863px">CASE STUDIES</a>
    <a href="#" style="left:960px">FAQS</a>
    <a href="#" style="left:1059px">CONTACT</a>
  </nav>
</header>

<section class="hero">
  <div class="hero-photo" role="img" aria-label="Smiling businessman in a dark shirt holding a tablet in a bright office"></div>
  <h1 class="hero-title">FLOWLINE – READY TO WORK END-TO-END<br>AUTOMATION</h1>
  <p class="hero-text">Increasing sales, streamlining processes, minimising errors and reducing costs are all possibilities when you automate your business using our Flowline platform.</p>
  <span class="slide-arrow" style="left:22px"></span>
  <span class="slide-arrow" style="right:22px"></span>
</section>

<section class="welcome">
  <h2 class="section-title">WELCOME TO PLUME ARC</h2>
  <div class="divider-icon"><span></span>
    <svg width="26" height="26" viewBox="0 0 26 26"><circle cx="13" cy="13" r="11" fill="none" stroke="#fff" stroke-width="2"/><circle cx="13" cy="13" r="6" fill="none" stroke="#fff" stroke-width="2"/><circle cx="13" cy="13" r="2" fill="#fff"/></svg>
  <span></span></div>
  <p>We've developed a range of solutions that can start revolutionising your business' supply chain process now. Or, we can help you make your custom software application, a reality.</p>
  <a href="#" class="btn-outline"><svg width="12" height="12" viewBox="0 0 12 12"><circle cx="6" cy="6" r="6" fill="#fff"/><path d="M5 3.5 7.5 6 5 8.5" stroke="#1f7fc0" stroke-width="1.6" fill="none"/></svg>READ MORE</a>
</section>

<section class="solutions">
  <h2 class="section-title">OUR SOLUTIONS</h2>
  <div class="divider-icon"><span style="width:160px"></span>
    <svg width="22" height="16" viewBox="0 0 22 16"><rect y="1" width="22" height="3" fill="#666"/><rect y="6.5" width="22" height="3" fill="#666"/><rect y="12" width="22" height="3" fill="#666"/></svg>
  <span style="width:160px"></span></div>
  <div class="solution-card" style="left:114px"><div class="photo" role="img" aria-label="Customer service team at an office desk" style="background:linear-gradient(135deg,#c9d3da,#6f7d88)"><div class="label">Customer service</div></div></div>
  <div class="solution-card" style="left:364px"><div class="photo" role="img" aria-label="Presenter showing business charts to colleagues" style="background:linear-gradient(135deg,#d7e2ea,#5d7f99)"><div class="label">Business Intelligence</div></div></div>
  <div class="solution-card" style="left:615px"><div class="photo" role="img" aria-label="Consultants meeting around a laptop" style="background:linear-gradient(135deg,#dde3e8,#7b8a96)"><div class="label">Advice and Consulting</div></div></div>
  <div class="solution-card" style="left:865px"><div class="photo" role="img" aria-label="Warehouse shelves stacked with boxes" style="background:linear-gradient(135deg,#e3b861,#8a5a1e)"><div class="label">Warehouse services</div></div></div>
  <div class="dots"><i></i><i class="on"></i></div>
</section>

<section class="features">
  <h2 class="col-title" style="left:112px">FEATURES</h2>
  <svg class="col-icon" style="left:112px" width="18" height="18" viewBox="0 0 18 18"><path d="M17 1 6 6l2 2-5 7 7-5 2 2z" fill="#444"/></svg>
  <div class="col-rule" style="left:140px;width:530px"></div>
  <ul class="bullets" style="left:112px;top:140px">
    <li>Product cataloguing</li><li>Product listing</li><li>Quoting</li><li>Sales team catalogue and quoting</li><li>E-Brochure creation</li>
  </ul>
  <ul class="bullets" style="left:386px;top:140px">
    <li>Inventory management</li><li>Warehouse scanning</li><li>Accounts and ERP system integration</li>
  </ul>
  <h2 class="col-title" style="left:700px">ARE YOU EXPERIENCING</h2>
  <svg class="col-icon" style="left:700px" width="18" height="18" viewBox="0 0 18 18"><path d="M2 8h3v9H2zM6 8l4-7c2 0 2 2 1.5 4H16c1 0 1.5 1 1 2l-2 8c-.3 1-1 2-2 2H6z" fill="none" stroke="#444" stroke-width="1.4"/></svg>
  <div class="col-rule" style="left:728px;width:360px"></div>
  <ul class="bullets" style="left:700px;top:140px">
    <li>A website that hasn't brought in enough sales</li>
    <li>Need for a warehousing system to keep handling costs down</li>
    <li>Need for a retail website – separate to your existing website</li>
    <li>Need more retail products drop shipped from more suppliers</li>
    <li>Requirement for distribution in your country or other countries</li>
  </ul>
  <div class="abs" style="left:112px;top:346px;width:976px;height:1px;background:var(--rule)"></div>
  <a href="#" class="btn-green abs" style="left:493px;top:384px;width:214px;height:59px"><svg width="14" height="11" viewBox="0 0 14 11"><rect width="14" height="11" rx="1" fill="#fff"/><path d="M0 1l7 5 7-5" stroke="#558a1a" stroke-width="1.3" fill="none"/></svg>CONTACT US</a>
</section>

<section class="services">
  <h2 class="section-title">AWESOME SERVICES</h2>
  <div class="divider-icon"><span style="width:110px"></span>
    <svg width="30" height="26" viewBox="0 0 30 26"><circle cx="11" cy="15" r="7" fill="none" stroke="#fff" stroke-width="4" stroke-dasharray="3 2.5"/><circle cx="11" cy="15" r="2.5" fill="#fff"/><circle cx="23" cy="7" r="4.5" fill="none" stroke="#fff" stroke-width="3" stroke-dasharray="2 2"/></svg>
  <span style="width:110px"></span></div>
  <p class="lead">Plume Arc specializes in Feature-rich Services.</p>
  <div class="service-card" style="left:112px">
    <div class="icon-box"><svg width="40" height="40" viewBox="0 0 40 40"><circle cx="20" cy="20" r="5" fill="#fff"/><path d="M10 10a14 14 0 0 0 0 20M30 10a14 14 0 0 1 0 20" stroke="#fff" stroke-width="3" fill="none"/></svg></div>
    <h3>BEACONS</h3><p style="top:170px">Enhance customer's in-store experience (Orchid)</p>
  </div>
  <div class="service-card" style="left:363px">
    <div class="icon-box"><svg width="26" height="42" viewBox="0 0 26 42"><rect x="2" y="2" width="22" height="38" rx="3" fill="none" stroke="#fff" stroke-width="3"/><circle cx="13" cy="34" r="2" fill="#fff"/></svg></div>
    <h3>NFC TAGS</h3><p style="top:170px">Enhance customer's in-store experience (Tessel)</p>
  </div>
  <div class="service-card" style="left:614px">
    <div class="icon-box"><svg width="40" height="40" viewBox="0 0 40 40"><circle cx="20" cy="20" r="17" fill="#fff"/><path d="M10 12c5 1 6 6 11 5s3 8-2 9M24 6c-2 4 2 6 6 5M22 34c2-4 7-5 9-9" stroke="#1a86c8" stroke-width="3" fill="none"/></svg></div>
    <h3>RFID TAGS</h3><p style="top:170px">Track global supply chains</p>
  </div>
  <div class="service-card" style="left:865px">
    <div class="icon-box"><svg width="40" height="40" viewBox="0 0 40 40"><circle cx="20" cy="20" r="17" fill="none" stroke="#fff" stroke-width="3"/><path d="M16 12v16l12-8z" fill="#fff"/></svg></div>
    <h3>VIDEO AND<br>MOVEMENT SENSORS</h3><p style="top:190px">For in-store retail insights</p>
  </div>
</section>

<section class="what-now">
  <div class="what-photo"><div role="img" aria-label="Hands reviewing printed business charts on a desk"></div></div>
  <h2>WHAT TO DO NOW</h2>
  <svg class="abs" style="left:476px;top:102px" width="20" height="18" viewBox="0 0 20 18"><path d="M19 1 1 8l6 2 2 7 3-5 5 3z" fill="none" stroke="#444" stroke-width="1.4"/></svg>
  <div class="abs" style="left:506px;top:112px;width:300px;height:1px;background:var(--rule)"></div>
  <p>If any of these situations are what you need, you're not alone. Many suppliers and manufacturers face these challenges. Plume Arc can help you create a marketing and sales plan for your situation, often incorporating our existing in-store and factory direct model using the Flowline supply chain.</p>
  <a href="#" class="btn-green abs" style="left:476px;top:246px;width:168px;height:52px"><svg width="14" height="11" viewBox="0 0 14 11"><rect width="14" height="11" rx="1" fill="#fff"/><path d="M0 1l7 5 7-5" stroke="#558a1a" stroke-width="1.3" fill="none"/></svg>CONTACT US</a>
</section>

<section class="partner">
  <h2 class="section-title">PARTNER WITH US TO DEVELOP A CUSTOM APP</h2>
  <div class="divider-icon"><span style="width:120px"></span>
    <svg width="24" height="24" viewBox="0 0 24 24"><path d="M6 2h12v6a6 6 0 0 1-12 0zM6 4H2c0 4 2 6 4 6M18 4h4c0 4-2 6-4 6M12 14v5M7 22h10" stroke="#fff" stroke-width="2" fill="none"/></svg>
  <span style="width:120px"></span></div>
  <p>Whether you have an app in mind that needs developing or a business process requiring special attention our 20 plus years experience in start-ups, media and retailing means we're the right people to help you bring it to life.</p>
</section>

<footer class="site-footer">
  <div class="footer-col" style="left:112px">
    <h4>CONNECT WITH US</h4>
    <p>We are an online sales management company.</p>
    <div class="social"><i></i><i></i><i></i><i></i><i></i></div>
  </div>
  <div class="footer-col" style="left:486px">
    <h4>NEWSLETTER</h4>
    <p>Signup Our Newsletter and Get News Updates</p>
    <div class="newsletter-form"><span>Email Address</span><b><svg width="12" height="12" viewBox="0 0 12 12"><path d="M6 1v10M1 6h10" stroke="#fff" stroke-width="2"/></svg></b></div>
  </div>
  <div class="footer-col" style="left:862px">
    <h4>CONTACT US</h4>
    <div class="contact-line"><i><svg width="12" height="12" viewBox="0 0 12 12"><path d="M2 1h3l1 3-2 1a7 7 0 0 0 3 3l1-2 3 1v3c-6 0-10-4-10-9z" fill="#ddd"/></svg></i>+61 2 9400 2718</div>
    <div class="contact-line"><i style="border:none"><svg width="14" height="11" viewBox="0 0 14 11"><rect width="14" height="11" rx="1" fill="#ddd"/><path d="M0 1l7 5 7-5" stroke="#1f2326" stroke-width="1.3" fill="none"/></svg></i>info@plumearc.com.au</div>
  </div>
</footer>

<div class="bottom-bar">Copyright@2016 Plume Arc | All Rights Reserved</div>

</body>
</html>
```